Flyer für Hersteller von Designertischen
Zielgruppe
Wir bauen Designer Tische, unser Zielgruppe liegt zwischen 35 und 50 Jahren
Aufgabenstellung
Wir legen Wert auf ein minimales Design, gerne in dem Stil unserer Website

```html
<!DOCTYPE html>
<html lang="en">
<head>
<meta charset="utf-8">
<title>Kessler Manufaktur – Flyer</title>
<link rel="stylesheet" href="https://fonts.googleapis.com/css2?family=Antonio:wght@100;200&family=Questrial&display=swap">
<style>
  :root {
    --page-bg: #d9dde1;
    --ink: #0b0b0c;
    --white: #ffffff;
    --tan: #c9a877;
    --text-soft: #e6e6e6;
    --wood-a: #d8c2a0;
    --wood-b: #6f7f8f;
    --bw-a: #2a2a2a;
    --bw-b: #8d8d8d;
  }
  * { margin: 0; padding: 0; box-sizing: border-box; }
  html, body { width: 1200px; height: 1200px; overflow: hidden; }
  body { background: var(--page-bg); position: relative; font-family: "Questrial", sans-serif; }

  .flyer {
    position: absolute; left: 204px; top: 40px;
    width: 792px; height: 1120px;
    background: var(--ink); overflow: hidden; color: var(--white);
  }
  .flyer > * { position: absolute; }

  .corner-mark { left: 46px; top: 36px; width: 84px; height: 84px; background: var(--white); }

  .brand { left: 450px; top: 36px; width: 220px; text-align: center; }
  .brand-dot { width: 66px; height: 66px; border: 3px solid var(--white); border-radius: 50%; margin: 0 auto 10px; }
  .brand-name { font-size: 11px; letter-spacing: 4px; color: var(--white); white-space: nowrap; }

  .hero-frame { left: 100px; top: 400px; width: 200px; height: 190px; background: var(--tan); }
  .hero-photo {
    left: 130px; top: 170px; width: 380px; height: 400px;
    background: linear-gradient(160deg, #3c3f48 0%, #6d6a66 40%, var(--wood-a) 70%, var(--wood-b) 100%);
  }
  .hero-word {
    left: 400px; top: 570px; width: 380px; height: 110px;
    transform: rotate(-90deg); transform-origin: left top;
    font-family: "Antonio", sans-serif; font-weight: 100; font-size: 110px; line-height: 110px;
    color: var(--white); white-space: nowrap; overflow: hidden;
  }

  .accent-square { left: 540px; top: 200px; width: 60px; height: 60px; background: var(--tan); }

  .headline { left: 530px; top: 270px; font-size: 46px; font-weight: 400; line-height: 1.08; letter-spacing: 1px; white-space: nowrap; }
  .headline .accent { color: var(--tan); }

  .rule { height: 14px; background: var(--tan); }
  .rule-right { left: 530px; top: 440px; width: 190px; }
  .rule-left { left: 40px; top: 690px; width: 180px; }

  .intro { left: 530px; top: 475px; width: 230px; font-size: 15px; line-height: 1.45; color: var(--text-soft); }
  .intro p + p { margin-top: 14px; }

  .name-heading { left: 40px; top: 622px; font-size: 50px; font-weight: 400; letter-spacing: 1px; line-height: 1; }

  .about { left: 40px; top: 722px; width: 390px; font-size: 14.5px; line-height: 1.45; color: var(--text-soft); }

  .phone-box {
    left: 40px; top: 922px; width: 390px; height: 64px; background: var(--white);
    display: flex; align-items: center; gap: 14px; padding-left: 22px;
    color: var(--ink); font-size: 28px; letter-spacing: 1px;
  }
  .phone-box svg { width: 22px; height: 22px; }

  .maker-photo {
    left: 462px; top: 702px; width: 300px; height: 300px;
    background: radial-gradient(circle at 55% 55%, var(--bw-b) 0%, var(--bw-a) 70%, #111 100%);
  }
  .maker-word {
    left: 470px; top: 710px;
    font-family: "Antonio", sans-serif; font-weight: 100; font-size: 60px; line-height: 1;
    color: var(--white); white-space: nowrap;
  }

  .contact { left: 470px; top: 1030px; font-size: 13px; line-height: 1; color: var(--text-soft); }
  .contact li { list-style: none; display: flex; align-items: center; gap: 12px; margin-bottom: 14px; }
  .contact svg { width: 14px; height: 14px; }
</style>
</head>
<body>
  <main class="flyer">
    <div class="corner-mark"></div>

    <div class="brand">
      <div class="brand-dot"></div>
      <div class="brand-name">KESSLER MANUFAKTUR</div>
    </div>

    <div class="hero-frame"></div>
    <div class="hero-photo" role="img" aria-label="Craftsman pouring resin onto a wooden river table in his workshop"></div>
    <div class="hero-word">FURNITURE</div>

    <div class="accent-square"></div>
    <h1 class="headline">THAT<br><span class="accent">TELLS</span><br>STORIES</h1>
    <div class="rule rule-right"></div>

    <div class="intro">
      <p>Welcome to the<br>Kessler manufacture.</p>
      <p>Our passion is to create timeless and durable furniture. Each of our tables is crafted with care and attention to detail to last a lifetime. Quality and consistency are our top priority.</p>
    </div>

    <h2 class="name-heading">KESSLER</h2>
    <div class="rule rule-left"></div>
    <p class="about">Are you curious about who I am and what I do? The best way to get to know me is to take a look at my gallery. Because how do you say it so beautifully? A picture is worth a thousand words! Visit my gallery and you will get an impression of my work and the style that makes up my work. If you can't find what you're looking for or you have a question about my work, feel free to contact me.</p>

    <div class="phone-box">
      <svg viewBox="0 0 24 24" aria-hidden="true"><path fill="#c9a877" d="M6.6 10.8a15.1 15.1 0 0 0 6.6 6.6l2.2-2.2c.3-.3.7-.4 1-.2 1.1.4 2.3.6 3.6.6.6 0 1 .4 1 1V20c0 .6-.4 1-1 1A17 17 0 0 1 3 4c0-.6.4-1 1-1h3.5c.6 0 1 .4 1 1 0 1.3.2 2.5.6 3.6.1.3 0 .7-.2 1z"/></svg>
      <span>0157/48203915</span>
    </div>

    <div class="maker-photo" role="img" aria-label="Black and white portrait of the craftsman leaning on a table in a tunnel"></div>
    <div class="maker-word">MANUFACTURE</div>

    <ul class="contact">
      <li>
        <svg viewBox="0 0 24 24" aria-hidden="true"><rect x="2" y="5" width="20" height="14" rx="2" fill="#c9a877"/><path d="M3 6l9 7 9-7" stroke="#0b0b0c" stroke-width="2" fill="none"/></svg>
        kessler_werkstatt@mailbox.de
      </li>
      <li>
        <svg viewBox="0 0 24 24" aria-hidden="true"><circle cx="12" cy="12" r="10" fill="#c9a877"/><path d="M2 12h20M12 2c3 3 3 17 0 20M12 2c-3 3-3 17 0 20" stroke="#0b0b0c" stroke-width="1.5" fill="none"/></svg>
        www.kessler-werkstatt.de
      </li>
    </ul>
  </main>
</body>
</html>
```